High-end construction company needs a business card design

We need a modern looking business card that draws people in, is memorable and looks so good people will want to sick it on their fridges.
On the first side what is needed are:
Logo
My name - Tomasz Brelwik
Title - Managing Director
Website - www.varkelt.co.uk
Email - tomasz@varkelt.co.uk
Telephone - 020 5194 6281
Mobile - 07845139072
On the back side was is needed is a list of all the services we provide:
-Kitchen Renovations
-Bathroom Renovations
-House Renovations
-Garage Conversions
-Extensions
-Loft Conversions
-Conservatories
-Carpentry
-Tiling
-Electrical
-Plumbing & Heating
-Bricklaying
-Landscaping
-Decorating
-Plastering
We would like the colours to be the same shades as on the logo with grey or black for the words.
Target Market(s)
Anyone who needs building work done
Contact Information for Business Card
This business card is for a construction company which strives to deliver excellent service and quality.
The look and feel of the card should represent this.
Requirements
Must have
- On the first side what is needed are:
Logo
My name - Tomasz Brelwik
Title - Managing Director
Website - www.varkelt.co.uk
Email - tomasz@varkelt.co.uk
Telephone - 020 5194 6281
Mobile - 07845139072
Nice to have
- Cool looking features

```html
<!DOCTYPE html>
<html lang="en">
<head>
<meta charset="utf-8">
<title>Varkelt Construction Ltd – Business Card</title>
<link rel="stylesheet" href="https://fonts.googleapis.com/css2?family=Libre+Franklin:wght@400;500&family=Montserrat:wght@500;800&display=swap">
<style>
  :root {
    --canvas: #d9dadb;
    --card: #333538;
    --card-shade: #2b2d30;
    --green-light: #7ac143;
    --green: #4f9e44;
    --green-dark: #3d8a36;
    --white: #ffffff;
  }
  * { box-sizing: border-box; margin: 0; padding: 0; }
  html, body { width: 1200px; height: 960px; overflow: hidden; }
  body {
    background: var(--canvas);
    font-family: "Libre Franklin", Arial, sans-serif;
    color: var(--white);
  }
  .card {
    position: absolute;
    left: 250px;
    width: 700px;
    height: 400px;
    background: linear-gradient(135deg, var(--card) 0%, var(--card-shade) 100%);
    overflow: hidden;
    box-shadow: 0 10px 30px rgba(0,0,0,.25);
  }
  .card--services { top: 60px; }
  .card--contact { top: 500px; }

  .brand {
    font-family: "Montserrat", Arial, sans-serif;
    font-weight: 800;
    color: var(--green-light);
    text-transform: uppercase;
    display: flex;
    align-items: center;
    gap: 14px;
    line-height: 1;
  }
  .brand__mark {
    width: 22px; height: 22px;
    background: var(--green-light);
    flex: none;
  }
  .brand__name { font-size: 44px; letter-spacing: 2px; }
  .brand__sub { display: block; font-size: 15px; letter-spacing: 4.5px; margin-top: 8px; }

  /* Services side */
  .card--services .brand {
    position: absolute; top: 58px; left: 0; right: 0; justify-content: center;
  }
  .services-heading {
    position: absolute; top: 170px; left: 110px; right: 110px;
    display: flex; align-items: center; gap: 16px;
    font-family: "Montserrat", Arial, sans-serif;
    font-weight: 800; font-size: 20px; letter-spacing: 1px;
    color: var(--green-light);
  }
  .services-heading::before, .services-heading::after {
    content: ""; flex: 1; height: 2px; background: var(--green);
  }
  .services-list {
    position: absolute; top: 214px; left: 20px; right: 20px;
    text-align: center; font-size: 17px; line-height: 28px; font-weight: 500;
  }
  .services-list li { list-style: none; }
  .services-list span::before {
    content: "•"; color: var(--green-light); margin: 0 6px 0 8px;
  }
  .services-band {
    position: absolute; left: 0; right: 0; bottom: 0; height: 36px; display: flex;
  }
  .services-band__left { flex: 1; background: var(--green); }
  .services-band__right { flex: 1; background: var(--green-light); border-left: 3px solid var(--card-shade); }

  /* Contact side */
  .swoosh { position: absolute; inset: 0; }
  .card--contact .brand { position: absolute; top: 130px; left: 60px; }
  .person { position: absolute; top: 46px; right: 50px; text-align: right; }
  .person__name {
    font-family: "Montserrat", Arial, sans-serif; font-weight: 800;
    font-size: 30px; color: var(--green-light); text-transform: uppercase; letter-spacing: .5px;
  }
  .person__title { font-size: 20px; margin-top: 4px; }
  .contact-list {
    position: absolute; top: 222px; right: 44px; list-style: none; text-align: right;
    font-size: 19px; line-height: 31px;
  }
  .contact-list li { display: flex; align-items: center; justify-content: flex-end; gap: 10px; }
  .contact-list svg { width: 18px; height: 18px; fill: none; stroke: var(--green-light); stroke-width: 1.8; }
</style>
</head>
<body>

<section class="card card--services" aria-label="Services side">
  <div class="brand">
    <span class="brand__mark"></span>
    <span><span class="brand__name">Varkelt</span><span class="brand__sub">Construction Ltd</span></span>
  </div>
  <h2 class="services-heading">SERVICES</h2>
  <ul class="services-list">
    <li><span>Kitchen Renovations</span><span>Bathroom Renovations</span><span>House Renovations</span></li>
    <li><span>Garage Conversions</span><span>Extensions</span><span>Loft Conversions</span><span>Conservatories</span></li>
    <li><span>Carpentry</span><span>Tiling</span><span>Electrical</span><span>Plumbing &amp; Heating</span></li>
    <li><span>Bricklaying</span><span>Landscaping</span><span>Decorating</span><span>Plastering</span></li>
  </ul>
  <div class="services-band">
    <div class="services-band__left"></div>
    <div class="services-band__right"></div>
  </div>
</section>

<section class="card card--contact" aria-label="Contact side">
  <svg class="swoosh" viewBox="0 0 700 400" preserveAspectRatio="none" aria-hidden="true">
    <defs>
      <linearGradient id="swoosh-fill" x1="0" y1="1" x2="1" y2="0">
        <stop offset="0" stop-color="#5aa84a"/>
        <stop offset="1" stop-color="#3d8a36"/>
      </linearGradient>
    </defs>
    <path d="M0,318 C230,240 450,150 700,92 L700,100 C450,160 230,250 0,330 Z" fill="#7ac143"/>
    <path d="M0,340 C240,262 460,170 700,110 L700,140 C470,196 250,300 0,400 Z" fill="#7ac143"/>
    <path d="M0,400 L0,392 C250,300 470,206 700,150 L700,400 Z" fill="url(#swoosh-fill)"/>
  </svg>

  <div class="brand">
    <span class="brand__mark"></span>
    <span><span class="brand__name">Varkelt</span><span class="brand__sub">Construction Ltd</span></span>
  </div>

  <div class="person">
    <p class="person__name">Tomasz Brelwik</p>
    <p class="person__title">Managing Director</p>
  </div>

  <ul class="contact-list">
    <li>020 5194 6281
      <svg viewBox="0 0 24 24"><path d="M5 3h4l2 5-3 2a12 12 0 0 0 6 6l2-3 5 2v4a2 2 0 0 1-2 2A18 18 0 0 1 3 5a2 2 0 0 1 2-2z"/></svg></li>
    <li>07845139072
      <svg viewBox="0 0 24 24"><rect x="7" y="2" width="10" height="20" rx="2"/><path d="M11 18h2"/></svg></li>
    <li>tomasz@varkelt.co.uk
      <svg viewBox="0 0 24 24"><rect x="3" y="5" width="18" height="14"/><path d="M3 5l9 8 9-8"/></svg></li>
    <li>www.varkelt.co.uk
      <svg viewBox="0 0 24 24"><circle cx="12" cy="12" r="9"/><path d="M3 12h18M12 3c3 3 3 15 0 18M12 3c-3 3-3 15 0 18"/></svg></li>
  </ul>
</section>

</body>
</html>
```